Existing Website Requiring new Pages

I have an existing word press website that was built using elementor.
Website: www.tallowcrestcare.com.au
I require the Vacancies page (https://www.tallowcrestcare.com.au/vacancies/) to be modified to display our new properties along with minor tweaks to how the information is presented.
The vacancies to be displayed are the exactly the same as those that are located on the homepage of QMR website (https://qmr.org.au/)
The new pages that link off the Vacancies tab will require custom design.
There are roughly 8 pages/properties to be incorporated. i wish for the design to be very similar to that displayed in the following link; https://www.polunda.com.au/vacancies/merrylands
Along with this the back end has not been updated for the last 3 years so it also requires some maintenance.
Website is in the disability industry and the custom pages will display information relative to Property Vacancies.
I have attached a ZIP file with some design guides, the information for each of the properties (which will need to be modified to show our business name Tallowcrest Care) and the example of how it is to look based off the Polunda website.
If you guys have any suggestions or ideas on how to make this more presentable or possible i'm open to your ideas.
Target Market(s)
People looking for SDA properties custom built for people with a disability
Industry/Entity Type
Disability
Coding
Coded - Design and coding required
Number of Pages Required
5+ page

```html
<!DOCTYPE html>
<html lang="en">
<head>
<meta charset="utf-8">
<title>Vacancies – Tallowcrest Care</title>
<link href="https://fonts.googleapis.com/css2?family=Montserrat:wght@400;500;600;700&display=swap" rel="stylesheet">
<style>
:root{
  --orange:#fbb862;
  --accent:#f7a23d;
  --ink:#1d1d1d;
  --nav:#3a3a3a;
  --muted:#7b7b7b;
  --line:#e3e3e3;
  --blue:#1aa3e8;
  --footer-bar:#000;
}
*{margin:0;padding:0;box-sizing:border-box}
html,body{width:707px;height:1200px;overflow:hidden;background:#fff;font-family:"Montserrat",sans-serif;color:var(--ink)}
.page{position:relative;width:707px;height:1200px}
.site-header{position:absolute;top:0;left:0;width:707px;height:81px;background:#fff}
.brand{position:absolute;left:37px;top:24px;display:flex;align-items:center;gap:6px;font-size:14px;font-weight:600;color:var(--ink)}
.brand-dot{width:14px;height:14px;border-radius:50%;background:var(--accent)}
.main-nav{position:absolute;top:36px;right:36px;display:flex;gap:16px;font-size:7px;font-weight:700;letter-spacing:.6px;color:var(--nav)}
.main-nav .active{color:var(--accent)}
.hero{position:absolute;top:81px;left:0;width:707px;height:327px;display:flex}
.hero-photo{width:449px;height:327px;background:linear-gradient(160deg,#d9d4cc 0%,#a89f92 45%,#4b4a48 80%,#1e1e1e 100%)}
.hero-panel{flex:1;background:var(--orange);position:relative}
.hero-mark{position:absolute;top:96px;left:0;right:0;text-align:center;font-size:12px;font-weight:500;color:#e9a555}
.hero-title{position:absolute;top:145px;left:0;right:0;text-align:center;font-size:31px;font-weight:700;color:#fff;letter-spacing:.5px}
.listings{position:absolute;top:459px;left:35px;display:grid;grid-template-columns:repeat(4,144px);column-gap:20px;row-gap:30px}
.card{width:144px;height:227px;border:1px solid var(--line);border-radius:3px;box-shadow:0 2px 8px rgba(0,0,0,.08);text-align:center;background:#fff;overflow:hidden}
.card-photo{height:102px}
.card-title{margin-top:12px;font-size:12px;font-weight:500;color:var(--accent)}
.card-type{margin-top:8px;font-size:9px;display:flex;justify-content:center;align-items:center;gap:6px}
.card-text{margin-top:7px;font-size:7.6px;line-height:12px;color:var(--muted);padding:0 8px}
.card-link{margin-top:8px;font-size:9px;font-weight:500;display:flex;justify-content:center;align-items:center;gap:5px}
.site-footer{position:absolute;top:1000px;left:0;width:707px}
.footer-brand{position:absolute;left:45px;top:40px;display:flex;align-items:center;gap:6px;font-size:16px;font-weight:600}
.contact{position:absolute;left:43px;top:97px;font-size:7.8px;color:var(--muted);line-height:13.5px}
.contact li{list-style:none;display:flex;align-items:center;gap:6px}
.socials{position:absolute;left:303px;top:3px;display:flex;flex-direction:column;gap:5px}
.socials span{width:20px;height:20px;border-radius:50%;display:block}
.col{position:absolute;top:0;width:143px}
.col h3{font-size:8.5px;font-weight:500;letter-spacing:.4px;border-left:2px solid var(--blue);padding-left:8px;margin-left:0;height:10px;line-height:10px}
.col ul{margin-top:9px;list-style:none;border-top:1px solid var(--line)}
.col li{font-size:7.6px;color:var(--muted);line-height:13.5px;padding:5px 0;border-bottom:1px solid var(--line)}
.bottom-bar{position:absolute;left:0;top:1157px;width:707px;height:43px;background:var(--footer-bar);color:#fff;font-size:8.8px;text-align:center;line-height:43px}
</style>
</head>
<body>
<div class="page">
  <header class="site-header">
    <div class="brand"><span class="brand-dot"></span>Tallowcrest Care</div>
    <nav class="main-nav">
      <span>HOME</span><span>ABOUT US</span><span class="active">WHAT WE DO ⌄</span><span>REFERRALS</span><span>FEEDBACK</span><span>CONTACT US</span>
    </nav>
  </header>

  <section class="hero">
    <div class="hero-photo" role="img" aria-label="Woman in a wheelchair working on a laptop at a desk in a bright living room"></div>
    <div class="hero-panel">
      <div class="hero-mark">Tallowcrest Care</div>
      <h1 class="hero-title">VACANCIES</h1>
    </div>
  </section>

  <main class="listings">
    <article class="card"><div class="card-photo" role="img" aria-label="Brick home with garage in Penrith" style="background:linear-gradient(180deg,#c9d4df 0%,#8b8a82 50%,#4e6b3b 100%)"></div><h2 class="card-title">Penrith</h2><div class="card-type"><svg width="13" height="10" viewBox="0 0 13 10"><rect x="1" y="1" width="11" height="4" rx="1" fill="none" stroke="#1d1d1d"/><rect x=".5" y="5" width="12" height="3" fill="none" stroke="#1d1d1d"/><path d="M1 8v2M12 8v2" stroke="#1d1d1d"/></svg>4 Bedroom SIL Home</div><p class="card-text">Lorem ipsum dolor sit amet, consectetur adipiscing elit, sed do eiusmod tempor</p><div class="card-link">Click Here <svg width="10" height="10" viewBox="0 0 10 10"><circle cx="5" cy="5" r="4.3" fill="none" stroke="#1d1d1d"/><path d="M4.2 3l2 2-2 2" fill="none" stroke="#1d1d1d"/></svg></div></article>
    <article class="card"><div class="card-photo" role="img" aria-label="Red brick home with hedge in Mount Druitt" style="background:linear-gradient(180deg,#9fb6c8 0%,#9a5f48 45%,#4f7a30 100%)"></div><h2 class="card-title">Mount Druitt</h2><div class="card-type"><svg width="13" height="10" viewBox="0 0 13 10"><rect x="1" y="1" width="11" height="4" rx="1" fill="none" stroke="#1d1d1d"/><rect x=".5" y="5" width="12" height="3" fill="none" stroke="#1d1d1d"/><path d="M1 8v2M12 8v2" stroke="#1d1d1d"/></svg>4 Bedroom SIL Home</div><p class="card-text">Lorem ipsum dolor sit amet, consectetur adipiscing elit, sed do eiusmod tempor</p><div class="card-link">Click Here <svg width="10" height="10" viewBox="0 0 10 10"><circle cx="5" cy="5" r="4.3" fill="none" stroke="#1d1d1d"/><path d="M4.2 3l2 2-2 2" fill="none" stroke="#1d1d1d"/></svg></div></article>
    <article class="card"><div class="card-photo" role="img" aria-label="Cream home with dark roof in Casula" style="background:linear-gradient(180deg,#a9cbe6 0%,#e8dfb4 50%,#3f6a2c 100%)"></div><h2 class="card-title">Casula</h2><div class="card-type"><svg width="13" height="10" viewBox="0 0 13 10"><rect x="1" y="1" width="11" height="4" rx="1" fill="none" stroke="#1d1d1d"/><rect x=".5" y="5" width="12" height="3" fill="none" stroke="#1d1d1d"/><path d="M1 8v2M12 8v2" stroke="#1d1d1d"/></svg>4 Bedroom SIL Home</div><p class="card-text">Lorem ipsum dolor sit amet, consectetur adipiscing elit, sed do eiusmod tempor</p><div class="card-link">Click Here <svg width="10" height="10" viewBox="0 0 10 10"><circle cx="5" cy="5" r="4.3" fill="none" stroke="#1d1d1d"/><path d="M4.2 3l2 2-2 2" fill="none" stroke="#1d1d1d"/></svg></div></article>
    <article class="card"><div class="card-photo" role="img" aria-label="Heritage cottage in Eastwood" style="background:linear-gradient(180deg,#b8c9d6 0%,#ddcbb2 50%,#6c6a45 100%)"></div><h2 class="card-title">Eastwood</h2><div class="card-type"><svg width="13" height="10" viewBox="0 0 13 10"><rect x="1" y="1" width="11" height="4" rx="1" fill="none" stroke="#1d1d1d"/><rect x=".5" y="5" width="12" height="3" fill="none" stroke="#1d1d1d"/><path d="M1 8v2M12 8v2" stroke="#1d1d1d"/></svg>4 Bedroom SIL Home</div><p class="card-text">Lorem ipsum dolor sit amet, consectetur adipiscing elit, sed do eiusmod tempor</p><div class="card-link">Click Here <svg width="10" height="10" viewBox="0 0 10 10"><circle cx="5" cy="5" r="4.3" fill="none" stroke="#1d1d1d"/><path d="M4.2 3l2 2-2 2" fill="none" stroke="#1d1d1d"/></svg></div></article>
    <article class="card"><div class="card-photo" role="img" aria-label="Orange brick home with driveway in Merrylands" style="background:linear-gradient(180deg,#8fb8e0 0%,#c9744a 45%,#8a8a86 100%)"></div><h2 class="card-title">Merrylands</h2><div class="card-type"><svg width="13" height="10" viewBox="0 0 13 10"><rect x="1" y="1" width="11" height="4" rx="1" fill="none" stroke="#1d1d1d"/><rect x=".5" y="5" width="12" height="3" fill="none" stroke="#1d1d1d"/><path d="M1 8v2M12 8v2" stroke="#1d1d1d"/></svg>4 Bedroom SIL Home</div><p class="card-text">Lorem ipsum dolor sit amet, consectetur adipiscing elit, sed do eiusmod tempor</p><div class="card-link">Click Here <svg width="10" height="10" viewBox="0 0 10 10"><circle cx="5" cy="5" r="4.3" fill="none" stroke="#1d1d1d"/><path d="M4.2 3l2 2-2 2" fill="none" stroke="#1d1d1d"/></svg></div></article>
    <article class="card"><div class="card-photo" role="img" aria-label="Brick home with palm tree in Baulkham Hills" style="background:linear-gradient(180deg,#7fb3e3 0%,#b88a66 50%,#4f8a2e 100%)"></div><h2 class="card-title">Baulkham Hills</h2><div class="card-type"><svg width="13" height="10" viewBox="0 0 13 10"><rect x="1" y="1" width="11" height="4" rx="1" fill="none" stroke="#1d1d1d"/><rect x=".5" y="5" width="12" height="3" fill="none" stroke="#1d1d1d"/><path d="M1 8v2M12 8v2" stroke="#1d1d1d"/></svg>4 Bedroom SIL Home</div><p class="card-text">Lorem ipsum dolor sit amet, consectetur adipiscing elit, sed do eiusmod tempor</p><div class="card-link">Click Here <svg width="10" height="10" viewBox="0 0 10 10"><circle cx="5" cy="5" r="4.3" fill="none" stroke="#1d1d1d"/><path d="M4.2 3l2 2-2 2" fill="none" stroke="#1d1d1d"/></svg></div></article>
    <article class="card"><div class="card-photo" role="img" aria-label="Property placeholder view for Greendale" style="background:linear-gradient(180deg,#a7c3dc 0%,#b39a72 45%,#3d5a33 100%)"></div><h2 class="card-title">Greendale</h2><div class="card-type"><svg width="13" height="10" viewBox="0 0 13 10"><rect x="1" y="1" width="11" height="4" rx="1" fill="none" stroke="#1d1d1d"/><rect x=".5" y="5" width="12" height="3" fill="none" stroke="#1d1d1d"/><path d="M1 8v2M12 8v2" stroke="#1d1d1d"/></svg>4 Bedroom SIL Home</div><p class="card-text">Lorem ipsum dolor sit amet, consectetur adipiscing elit, sed do eiusmod tempor</p><div class="card-link">Click Here <svg width="10" height="10" viewBox="0 0 10 10"><circle cx="5" cy="5" r="4.3" fill="none" stroke="#1d1d1d"/><path d="M4.2 3l2 2-2 2" fill="none" stroke="#1d1d1d"/></svg></div></article>
    <article class="card"><div class="card-photo" role="img" aria-label="Property placeholder view for Bringelly" style="background:linear-gradient(180deg,#4d6479 0%,#6f7a55 50%,#3a4a2a 100%)"></div><h2 class="card-title">Bringelly</h2><div class="card-type"><svg width="13" height="10" viewBox="0 0 13 10"><rect x="1" y="1" width="11" height="4" rx="1" fill="none" stroke="#1d1d1d"/><rect x=".5" y="5" width="12" height="3" fill="none" stroke="#1d1d1d"/><path d="M1 8v2M12 8v2" stroke="#1d1d1d"/></svg>4 Bedroom SIL Home</div><p class="card-text">Lorem ipsum dolor sit amet, consectetur adipiscing elit, sed do eiusmod tempor</p><div class="card-link">Click Here <svg width="10" height="10" viewBox="0 0 10 10"><circle cx="5" cy="5" r="4.3" fill="none" stroke="#1d1d1d"/><path d="M4.2 3l2 2-2 2" fill="none" stroke="#1d1d1d"/></svg></div></article>
  </main>

  <footer class="site-footer">
    <div class="footer-brand"><span class="brand-dot"></span>Tallowcrest Care</div>
    <ul class="contact">
      <li><svg width="9" height="7" viewBox="0 0 9 7"><rect x=".5" y=".5" width="8" height="6" fill="none" stroke="#f0457a"/><path d="M.5 .5l4 3.2 4-3.2" fill="none" stroke="#f0457a"/></svg>Email: info@tallowcrestcare.com.au</li>
      <li><svg width="9" height="9" viewBox="0 0 9 9"><path d="M1.5 1l2 .2.6 2-1 .8a5 5 0 0 0 2 2l.8-1 2 .6.2 2c-4 .6-7.2-2.6-6.6-6.6z" fill="#f0457a"/></svg>Phone: +61 0491 570 156</li>
      <li><svg width="9" height="9" viewBox="0 0 9 9"><circle cx="4.5" cy="4.5" r="3.8" fill="none" stroke="#f0457a"/><path d="M4.5 2.2v2.5l1.6 1" fill="none" stroke="#f0457a"/></svg>Operating Hours: 9AM To 5PM Monday - Friday</li>
    </ul>
    <div class="socials">
      <span style="background:#6b2a7e"></span>
      <span style="background:#2f5fa7"></span>
      <span style="background:#1c1c1c"></span>
      <span style="background:#1a7fb8"></span>
    </div>
    <div class="col" style="left:361px">
      <h3>ACCOMMODATION</h3>
      <ul>
        <li>Supported Independent Living (SIL)</li>
        <li>Specialist Disability Accommodation (SDA)</li>
        <li>Short term Accommodation (Respite)</li>
        <li>Vacancies</li>
      </ul>
    </div>
    <div class="col" style="left:520px">
      <h3>WHAT WE DO</h3>
      <ul>
        <li>In Home Care</li>
        <li>Social &amp; Community Services</li>
        <li>Therapeutic Supports</li>
        <li>Support Coordination</li>
        <li>Home Modifications</li>
      </ul>
    </div>
  </footer>
  <div class="bottom-bar">© Copyright 2024 | Tallowcrest Care | All Rights Reserved.</div>
</div>
</body>
</html>
```